UK Online Auction Site needs a clever design

We need a contemporary landing page and registration page design for a UK auction website, that look equally at home on PC's and tablets . The design should be fresh, bright, clean, professional, robust, and familiar. We would like to see something clever but functional.

Online

```html
<!DOCTYPE html>
<html lang="en">
<head>
<meta charset="utf-8">
<title>Bidwell – Online Auctions</title>
<link rel="stylesheet" href="https://fonts.googleapis.com/css2?family=Open+Sans:wght@400;600&family=Roboto+Condensed:wght@300;400;700&family=Roboto:wght@400&display=swap">
<style>
:root{
  --page:#f6f7f9;
  --blue:#0f8bd8;
  --blue-dark:#0a6fb5;
  --blue-light:#2aa7ee;
  --orange:#f7a21b;
  --green:#6cc024;
  --green-dark:#4f9d12;
  --ink:#2b2b2b;
  --grey:#6b6b6b;
  --footer:#1c1c1c;
  --footer-text:#d8d8d8;
  --caption:rgba(20,20,20,.78);
}
*{box-sizing:border-box;margin:0;padding:0}
html,body{width:712px;height:1200px;overflow:hidden}
body{background:var(--page);font-family:"Open Sans",sans-serif;color:var(--ink);position:relative}
.abs{position:absolute}

/* header */
.brand{left:64px;top:14px;display:flex;align-items:center;gap:6px;font-family:"Roboto Condensed",sans-serif;font-weight:700;font-size:30px;color:var(--blue)}
.brand-dot{width:12px;height:12px;border-radius:50%;background:var(--blue)}
.nav{top:30px;left:294px;display:flex;align-items:center;font-family:"Roboto Condensed",sans-serif;font-size:10px;color:var(--ink);height:18px}
.nav-item{display:flex;align-items:center;gap:3px;padding:0 6px;border-right:1px solid #ccc;line-height:10px}
.nav-item:last-of-type{border-right:none}
.nav-sell{background:var(--blue);color:#fff;border-radius:9px;height:18px;padding:0 9px;margin-right:5px;border:none}
.nav svg{width:8px;height:8px;fill:currentColor}
.register{left:586px;top:30px;width:62px;height:18px;border-radius:9px;background:var(--green);color:#fff;font-family:"Roboto Condensed",sans-serif;font-size:9px;display:flex;align-items:center;justify-content:center;gap:3px}
.register svg{width:7px;height:7px;fill:#fff}

/* search */
.search-bar{left:64px;top:71px;width:584px;height:32px;background:linear-gradient(#2aa0e8,#0b70b8);border-radius:1px}
.search-field{left:94px;top:76px;width:416px;height:22px;background:#fff;border-radius:11px;display:flex;align-items:center;font-size:7.5px;color:#444}
.search-cat{width:124px;height:100%;border-right:1px solid #ddd;padding-left:11px;display:flex;align-items:center;justify-content:space-between;padding-right:10px}
.search-text{padding-left:12px}
.search-btn{left:521px;top:75px;width:98px;height:24px;border-radius:12px;background:linear-gradient(#ffb12e,#f08c0c);color:#fff;font-family:"Roboto Condensed",sans-serif;font-size:13px;display:flex;align-items:center;justify-content:center;gap:5px}
.search-btn svg{width:10px;height:10px}

/* hero */
.hero{left:64px;top:115px;width:584px;height:225px;background:linear-gradient(110deg,#fbe6f4,#f5b8e2 60%,#f1a6d8);overflow:hidden}
.hero-model{position:absolute;right:0;top:0;width:250px;height:225px;background:linear-gradient(90deg,rgba(0,0,0,0),#d49ab8 35%,#7a5a6e 70%,#2f3d6a)}
.hero-kicker{left:98px;top:138px;font-family:"Roboto Condensed",sans-serif;font-weight:300;font-size:30px;color:#222;letter-spacing:.5px}
.hero-deal{left:96px;top:166px;font-family:"Roboto Condensed",sans-serif;font-weight:300;font-size:74px;line-height:1;letter-spacing:-1px}
.hero-deal .pct{color:var(--orange)}
.hero-deal .off{color:var(--blue)}
.hero-sub{left:98px;top:241px;font-family:"Open Sans",sans-serif;font-size:17px;color:#222}
.shop-btn{left:98px;top:272px;width:106px;height:29px;border-radius:15px;background:linear-gradient(#82d22f,#52a60f);color:#fff;font-family:"Open Sans",sans-serif;font-size:12px;display:flex;align-items:center;justify-content:center;gap:4px;box-shadow:0 2px 0 var(--green-dark)}
.shop-btn svg{width:9px;height:9px;fill:#fff}

/* section titles */
.section-title{left:0;width:712px;text-align:center;font-family:"Roboto Condensed",sans-serif;font-size:34px;color:var(--blue);font-weight:300}
.section-title b{font-weight:700}

/* intro */
.intro-photo{left:86px;top:426px;width:255px;height:141px;background:linear-gradient(90deg,#f6c2d9,#e8a1bf 50%,#f3c3d6)}
.intro-heading{left:366px;top:420px;font-family:"Roboto Condensed",sans-serif;font-size:13px;color:var(--blue)}
.intro-copy{left:366px;top:438px;width:256px;font-family:"Roboto",sans-serif;font-size:8.4px;line-height:12.6px;color:var(--grey)}
.learn-btn{left:366px;top:542px;width:82px;height:18px;border-radius:9px;background:var(--green);color:#fff;font-size:7.5px;display:flex;align-items:center;justify-content:center;gap:4px}

.products-lead{left:0;top:644px;width:712px;text-align:center;font-size:10px;color:#333}

/* product grid */
.grid{left:63px;top:686px;display:grid;grid-template-columns:repeat(4,138px);column-gap:11px;row-gap:13px}
.card{position:relative;height:177px;overflow:hidden;border-radius:1px}
.card-photo{position:absolute;inset:0}
.card-caption{position:absolute;left:0;right:0;bottom:0;height:38px;background:var(--caption);color:#fff;text-align:center;padding-top:7px}
.card-title{font-size:10.5px;font-weight:600;line-height:13px}
.card-link{font-size:6.5px;line-height:10px}
.card-feature{background:var(--blue-light);color:#fff;text-align:center;padding-top:34px}
.card-feature .feature-brand{font-family:"Roboto Condensed",sans-serif;font-weight:700;font-size:20px}
.card-feature .card-title{margin-top:6px;font-size:11px}
.card-feature p{font-size:6.8px;line-height:9.5px;margin:5px 12px 0}
.feature-btn{display:inline-block;margin-top:8px;border:1px solid #fff;font-size:6.5px;padding:4px 8px}

/* footer */
.footer{left:0;top:1086px;width:712px;height:114px;background:var(--footer);color:var(--footer-text)}
.footer h4{position:absolute;font-family:"Roboto Condensed",sans-serif;font-weight:400;font-size:10px;color:#fff}
.footer a{position:absolute;font-size:7px;color:var(--footer-text);text-decoration:none}
.social{position:absolute;left:420px;display:flex;align-items:center;gap:7px;font-size:7.5px;color:var(--footer-text)}
.social i{display:block;width:17px;height:17px;border-radius:1px}
.footer-brand{position:absolute;left:546px;top:16px;font-family:"Roboto Condensed",sans-serif;font-weight:700;font-size:30px;color:#4a4a4a}
.copyright{position:absolute;right:64px;top:77px;text-align:right;font-size:7.2px;line-height:9px}
</style>
</head>
<body>

<header>
  <div class="abs brand"><span class="brand-dot"></span>Bidwell</div>
  <nav class="abs nav">
    <span class="nav-item nav-sell"><svg viewBox="0 0 10 10"><path d="M1 1h4l4 4-4 4-4-4z"/></svg>Sell ▾</span>
    <span class="nav-item"><svg viewBox="0 0 10 10"><circle cx="5" cy="3" r="2.3"/><path d="M1 10c0-3 2-4.5 4-4.5S9 7 9 10z"/></svg>Sign Up ▾</span>
    <span class="nav-item"><svg viewBox="0 0 10 10"><path d="M0 4h10l-1.5 5h-7z M3 4l2-3 2 3" /></svg>Basket ▾</span>
    <span class="nav-item"><svg viewBox="0 0 10 10"><circle cx="5" cy="5" r="5"/></svg>Help</span>
    <span class="nav-item"><svg viewBox="0 0 10 10"><path d="M0 2h10v6H0z"/></svg>Contact</span>
  </nav>
  <div class="abs register"><svg viewBox="0 0 10 10"><circle cx="5" cy="3" r="2.3"/><path d="M1 10c0-3 2-4.5 4-4.5S9 7 9 10z"/></svg>Register</div>
</header>

<div class="abs search-bar"></div>
<div class="abs search-field">
  <div class="search-cat">All Categories <span>▾</span></div>
  <div class="search-text">Search for a brand,product or specific item</div>
</div>
<div class="abs search-btn"><svg viewBox="0 0 10 10"><circle cx="4" cy="4" r="3" fill="none" stroke="#fff" stroke-width="1.6"/><path d="M6.2 6.2L9.3 9.3" stroke="#fff" stroke-width="1.8"/></svg>Search</div>

<section class="abs hero">
  <div class="hero-model" role="img" aria-label="Model wearing a necklace and earrings on a pink bokeh background"></div>
</section>
<div class="abs hero-kicker">JEWELLERY &amp; BEAUTY</div>
<div class="abs hero-deal"><span class="pct">25%</span> <span class="off">OFF</span></div>
<div class="abs hero-sub">ONLINE &amp; IN STORE</div>
<div class="abs shop-btn"><svg viewBox="0 0 10 10"><path d="M0 4h10l-1.5 5h-7z"/></svg>Shop Now</div>

<h2 class="abs section-title" style="top:366px"><b>Hi There</b> Nice to meet you</h2>
<div class="abs intro-photo" role="img" aria-label="Three women with styled hair on a pink background"></div>
<h3 class="abs intro-heading" style="font-weight:400">Lets talk about Bidwell</h3>
<p class="abs intro-copy">It is a long established fact that a reader will be distracted by the readable content of a page when looking at its layout. The point of using Lorem Ipsum is that it has a more-or-less normal distribution of letters, as opposed to using 'Content here, content here', making it look like readable English. Many desktop publishing packages and web page editors now use Lorem Ipsum as their default model text.</p>
<div class="abs learn-btn">Learn More <span>⟶</span></div>

<h2 class="abs section-title" style="top:602px"><b>Top</b> Products</h2>
<p class="abs products-lead">It is a long established fact that a reader will be distracted by the readable content.</p>

<section class="abs grid">
  <article class="card"><div class="card-photo" role="img" aria-label="Fashion model in a red knit and scarf" style="background:linear-gradient(160deg,#3a3432,#b8423d 55%,#2a2523)"></div><div class="card-caption"><div class="card-title">Fashion</div><div class="card-link">See All Product →</div></div></article>
  <article class="card"><div class="card-photo" role="img" aria-label="House with a garden and trees" style="background:linear-gradient(#7da94f,#c9c8c0 50%,#6b8f3d)"></div><div class="card-caption"><div class="card-title">Home &amp; Garden</div><div class="card-link">See All Product →</div></div></article>
  <article class="card card-feature">
    <div class="feature-brand">Bidwell</div>
    <div class="card-title">Electricals &amp; Technology</div>
    <p>It is a long established fact that a reader will be distracted by the readable content</p>
    <span class="feature-btn">See All Product →</span>
  </article>
  <article class="card"><div class="card-photo" role="img" aria-label="Bright bathroom interior with chandelier" style="background:linear-gradient(120deg,#f1efea,#d9d2c6 60%,#bcae98)"></div><div class="card-caption"><div class="card-title">Collectables &amp; Aniques</div><div class="card-link">See All Product →</div></div></article>
  <article class="card"><div class="card-photo" role="img" aria-label="Woman wearing gold jewellery" style="background:linear-gradient(160deg,#f7e6ef,#d9a77f 50%,#f2e2ea)"></div><div class="card-caption"><div class="card-title">Jewellery &amp; Beauty</div><div class="card-link">See All Product →</div></div></article>
  <article class="card"><div class="card-photo" role="img" aria-label="White teddy bear toy" style="background:linear-gradient(140deg,#d9b678,#efe6d8 45%,#c9a165)"></div><div class="card-caption"><div class="card-title">Toy</div><div class="card-link">See All Product →</div></div></article>
  <article class="card"><div class="card-photo" role="img" aria-label="Bowling ball and pins in a bowling alley" style="background:linear-gradient(#3b4d60,#a58a6e 50%,#2e4a58)"></div><div class="card-caption"><div class="card-title">Sport &amp; Leisure</div><div class="card-link">See All Product →</div></div></article>
  <article class="card"><div class="card-photo" role="img" aria-label="Black sports motorcycle" style="background:linear-gradient(140deg,#4a4a4a,#1d1d1d 60%,#333)"></div><div class="card-caption"><div class="card-title">Motors</div><div class="card-link">See All Product →</div></div></article>
</section>

<footer class="abs footer">
  <h4 style="left:65px;top:24px">Site Map</h4>
  <a style="left:65px;top:41px">Contact</a><a style="left:65px;top:55px">Terms</a><a style="left:65px;top:69px">Privacy</a><a style="left:65px;top:84px">RSS</a>
  <a style="left:122px;top:41px">About</a><a style="left:122px;top:55px">News</a><a style="left:122px;top:69px">Feeds</a>
  <h4 style="left:207px;top:24px">Buy</h4>
  <a style="left:207px;top:44px">Categories</a><a style="left:207px;top:58px">Search</a><a style="left:207px;top:73px">Currency</a><a style="left:207px;top:87px">Converter</a>
  <h4 style="left:303px;top:24px">Sell</h4>
  <a style="left:303px;top:44px">Sell New Item</a><a style="left:303px;top:58px">Sell Bulk Items</a>
  <h4 style="left:420px;top:19px">Follow Us</h4>
  <div class="social" style="top:36px"><i style="background:#3b5b98"></i>Friendline</div>
  <div class="social" style="top:58px"><i style="background:#2aa9e0"></i>Chirpnet</div>
  <div class="social" style="top:80px"><i style="background:#d9433a"></i>Circleplus</div>
  <div class="footer-brand">Bidwell</div>
  <div class="copyright">Copyright Bidwell ® 2003-13. All<br>rights reserved</div>
</footer>

</body>
</html>
```